Business Card Design Project - del varosi group

dear Sirs

we need business card design for our group ( DEL Varosi Group ) , i have got the Logo design of our group from pixel harbor in previous , so all need details relating to our group i think available with you, as well as the the chosen logo design

we hope to provide us with business card logo that to be appropaite and satisfactory to us .

thanks

note : logo design of our group is attached .
Updates

Reason: please extend the deadline of my project for additional 15 days because i didn't received appropriate design for our gruop yet . kindly beaware that i have received 77 design till now , supossed to send me 200-250 design at least . thanks

Target Market(s)

contents

name : Kerem EL Nadiri

position : Operation Manager

Industry/Entity Type

Business

Requirements
Must have

• person name

group logo
Nice to have
• logo color matching with back background

```html
<!DOCTYPE html>
<html lang="en">
<head>
<meta charset="utf-8">
<title>DEL Varosi Group – Business Card</title>
<link rel="stylesheet" href="https://fonts.googleapis.com/css2?family=Didact+Gothic&display=swap">
<style>
  :root {
    --page-bg: #e4e5e7;
    --card-bg: #f1eff0;
    --brand-blue: #1d4f93;
    --ink: #2d2d2d;
    --rule: #555555;
    --decor-tone: #e6e3e5;
    --card-shadow: rgba(0, 0, 0, 0.18);
  }
  * { box-sizing: border-box; margin: 0; padding: 0; }
  html, body {
    width: 1067px;
    height: 1200px;
    overflow: hidden;
  }
  body {
    background: var(--page-bg);
    font-family: "Didact Gothic", sans-serif;
    color: var(--ink);
    position: relative;
  }
  .card {
    position: absolute;
    left: 154px;
    width: 760px;
    height: 434px;
    background: var(--card-bg);
    box-shadow: 0 6px 22px var(--card-shadow);
    overflow: hidden;
  }
  .card--front { top: 100px; }
  .card--back { top: 666px; }

  .card__decor {
    position: absolute;
    top: 0;
    right: 0;
    width: 470px;
    height: 300px;
    background: linear-gradient(100deg, var(--card-bg) 0%, var(--decor-tone) 55%, var(--card-bg) 100%);
  }

  .brand {
    position: absolute;
    display: flex;
    align-items: center;
    gap: 12px;
    color: var(--brand-blue);
  }
  .brand__mark {
    width: 18px;
    height: 18px;
    background: var(--brand-blue);
    flex: none;
  }
  .brand__name {
    display: flex;
    flex-direction: column;
    line-height: 1;
  }
  .brand__title { letter-spacing: 1px; }
  .brand__sub { letter-spacing: 0.5px; }

  .card--front .brand { left: 46px; top: 40px; }
  .card--front .brand__title { font-size: 44px; }
  .card--front .brand__sub { font-size: 19px; margin-top: 4px; }

  .card--back .brand { left: 178px; top: 160px; }
  .card--back .brand__mark { width: 24px; height: 24px; }
  .card--back .brand__title { font-size: 62px; }
  .card--back .brand__sub { font-size: 26px; margin-top: 6px; align-self: flex-end; }

  .person {
    position: absolute;
    left: 58px;
    top: 252px;
  }
  .person__name {
    font-size: 24px;
    letter-spacing: 0.5px;
    text-transform: uppercase;
  }
  .person__role {
    font-size: 16px;
    margin-top: 2px;
  }

  .divider {
    position: absolute;
    left: 58px;
    right: 48px;
    top: 310px;
    border-top: 2px solid var(--rule);
  }

  .contacts {
    position: absolute;
    left: 58px;
    top: 326px;
    display: grid;
    grid-template-columns: 344px 300px;
  }
  .contacts__col {
    display: flex;
    flex-direction: column;
    gap: 12px;
  }
  .contact {
    display: flex;
    align-items: center;
    gap: 14px;
    font-size: 15px;
    height: 22px;
  }
  .contact--plain { padding-left: 38px; }
  .contact__icon {
    width: 22px;
    height: 22px;
    flex: none;
    fill: var(--ink);
  }
</style>
</head>
<body>

  <section class="card card--front" aria-label="Business card front">
    <div class="card__decor" role="img" aria-label="Faint grey decorative swoosh pattern"></div>

    <div class="brand">
      <span class="brand__mark"></span>
      <span class="brand__name">
        <span class="brand__title">DEL VAROSI</span>
        <span class="brand__sub">GROUP OF COMPANIES</span>
      </span>
    </div>

    <div class="person">
      <p class="person__name">Kerem EL Nadiri</p>
      <p class="person__role">Operation manager</p>
    </div>

    <div class="divider"></div>

    <div class="contacts">
      <div class="contacts__col">
        <p class="contact">
          <svg class="contact__icon" viewBox="0 0 24 24" aria-hidden="true"><path d="M7 2h10a1 1 0 0 1 1 1v18a1 1 0 0 1-1 1H7a1 1 0 0 1-1-1V3a1 1 0 0 1 1-1zm1 3v12h8V5H8zm4 13.5a1 1 0 1 0 0 2 1 1 0 0 0 0-2z"/></svg>
          +36 555 010 204
        </p>
        <p class="contact">
          <svg class="contact__icon" viewBox="0 0 24 24" aria-hidden="true"><path d="M12 2a10 10 0 1 0 5 18.7l-1-1.7A8 8 0 1 1 20 12v1a2 2 0 0 1-4 0V7h-2v1a5 5 0 1 0 .6 6.9A4 4 0 0 0 22 13v-1A10 10 0 0 0 12 2zm0 13a3 3 0 1 1 0-6 3 3 0 0 1 0 6z"/></svg>
          info@delvarosi.example
        </p>
        <p class="contact">
          <svg class="contact__icon" viewBox="0 0 24 24" aria-hidden="true"><path d="M12 2a10 10 0 1 0 0 20 10 10 0 0 0 0-20zm6.9 6h-3a15 15 0 0 0-1.3-3.9A8 8 0 0 1 18.9 8zM12 4c.8 1.1 1.5 2.5 1.9 4h-3.8c.4-1.5 1.1-2.9 1.9-4zM4.3 14a8 8 0 0 1 0-4h3.4a16 16 0 0 0 0 4H4.3zm.8 2h3a15 15 0 0 0 1.3 3.9A8 8 0 0 1 5.1 16zm3-8h-3a8 8 0 0 1 4.3-3.9A15 15 0 0 0 8.1 8zM12 20c-.8-1.1-1.5-2.5-1.9-4h3.8c-.4 1.5-1.1 2.9-1.9 4zm2.3-6H9.7a14 14 0 0 1 0-4h4.6a14 14 0 0 1 0 4zm.3 5.9a15 15 0 0 0 1.3-3.9h3a8 8 0 0 1-4.3 3.9zm1.7-5.9a16 16 0 0 0 0-4h3.4a8 8 0 0 1 0 4h-3.4z"/></svg>
          www.delvarosi.example
        </p>
      </div>
      <div class="contacts__col">
        <p class="contact">
          <svg class="contact__icon" viewBox="0 0 24 24" aria-hidden="true"><path d="M12 3 1 12h3v9h6v-6h4v6h6v-9h3L12 3z"/></svg>
          P.O. Box: City name, etc.
        </p>
        <p class="contact contact--plain">Country name</p>
        <p class="contact">
          <svg class="contact__icon" viewBox="0 0 24 24" aria-hidden="true"><path d="M6 2h9l3 3v4h1a2 2 0 0 1 2 2v9a2 2 0 0 1-2 2H5a2 2 0 0 1-2-2v-9a2 2 0 0 1 2-2h1V2zm2 2v5h8V6h-2V4H8zm-1 9v2h2v-2H7zm4 0v2h2v-2h-2zm4 0v2h2v-2h-2zm-8 4v2h2v-2H7zm4 0v2h2v-2h-2zm4 0v2h2v-2h-2z"/></svg>
          Fax: 0555 010 205
        </p>
      </div>
    </div>
  </section>

  <section class="card card--back" aria-label="Business card back">
    <div class="card__decor" role="img" aria-label="Faint grey decorative swoosh pattern"></div>

    <div class="brand">
      <span class="brand__mark"></span>
      <span class="brand__name">
        <span class="brand__title">DEL VAROSI</span>
        <span class="brand__sub">GROUP OF COMPANIES</span>
      </span>
    </div>
  </section>

</body>
</html>
```